plumbers buisness card

A buisness card for a plumbing buisness
needs to have a water theme with navy blue, light blue and white
with an image of either a water drop, pipes, tools or something relating to plumbing and incorperating my buisness name as a logo

"Kettering Plumbing" is the words that need to stand out with "& gasfitting" to be smaller

spelling error on brief, "maintenance"
and also could you include my email d_kettering@mailwave.com.au

Industry/Entity Type

Plumbing

Contact Information for Business Card

Kettering Plumbing & Gasfitting

declan kettering
0432961085

specialising in
-new homes
-maitenance
-renovations

license no.
-73840

```html
<!DOCTYPE html>
<html lang="en">
<head>
<meta charset="utf-8">
<title>Kettering Plumbing — Business Card</title>
<link rel="stylesheet" href="https://fonts.googleapis.com/css2?family=Great+Vibes&family=Tinos&family=Montserrat:wght@400&display=swap">
<style>
  :root {
    --navy: #1a1fd6;
    --sky: #4fb6e8;
    --aqua: #a9e6ef;
    --deep: #1236c9;
    --white: #ffffff;
    --ink: #141414;
  }
  html, body {
    margin: 0;
    padding: 0;
    width: 1200px;
    height: 686px;
    overflow: hidden;
    background: var(--white);
  }
  .card {
    position: relative;
    width: 1200px;
    height: 686px;
    overflow: hidden;
    background: var(--white);
  }
  .card__waves {
    position: absolute;
    inset: 0;
  }
  .card__license,
  .card__contact,
  .card__email {
    position: absolute;
    margin: 0;
    font-family: "Tinos", "Times New Roman", serif;
    font-weight: 400;
    color: var(--navy);
    line-height: 1;
  }
  .card__license,
  .card__contact {
    top: 52px;
    font-size: 18px;
    letter-spacing: 0.02em;
  }
  .card__license { left: 35px; }
  .card__contact { right: 35px; }
  .card__email {
    top: 80px;
    right: 35px;
    font-size: 16px;
    letter-spacing: 0.02em;
  }
  .brand {
    position: absolute;
    left: 0;
    top: 0;
    width: 1200px;
    height: 360px;
    margin: 0;
    font-family: "Great Vibes", "Brush Script MT", cursive;
    font-weight: 400;
    color: var(--sky);
  }
  .brand__name {
    position: absolute;
    left: 0;
    width: 1200px;
    top: 198px;
    text-align: center;
    font-size: 86px;
    line-height: 1;
  }
  .brand__tagline {
    position: absolute;
    left: 752px;
    top: 288px;
    font-size: 48px;
    line-height: 1;
  }
  .services {
    position: absolute;
    left: 0;
    right: 0;
    top: 377px;
    margin: 0;
    text-align: center;
    font-family: "Montserrat", Arial, sans-serif;
    font-size: 21px;
    letter-spacing: 0.07em;
    line-height: 1;
    color: var(--navy);
  }
  .card__illustration {
    position: absolute;
    left: 903px;
    top: 400px;
    width: 263px;
    height: 257px;
    border-radius: 6px;
    background: linear-gradient(160deg, #2a2f3a 0%, var(--ink) 70%);
  }
</style>
</head>
<body>
<main class="card">
  <svg class="card__waves" width="1200" height="686" viewBox="0 0 1200 686" aria-hidden="true">
    <defs>
      <linearGradient id="haze" x1="0" y1="0" x2="0" y2="1">
        <stop offset="0" stop-color="#ffffff" stop-opacity="0"/>
        <stop offset="0.55" stop-color="#c9eff4"/>
        <stop offset="1" stop-color="#7ecbe8"/>
      </linearGradient>
      <linearGradient id="swoosh" x1="0" y1="0" x2="1" y2="0">
        <stop offset="0" stop-color="#1236c9" stop-opacity="0.2"/>
        <stop offset="0.35" stop-color="#1a3fe0"/>
        <stop offset="0.75" stop-color="#6aa8ee"/>
        <stop offset="1" stop-color="#cfe3fb" stop-opacity="0.6"/>
      </linearGradient>
      <linearGradient id="light" x1="0" y1="0" x2="1" y2="0">
        <stop offset="0" stop-color="#8fd9ea"/>
        <stop offset="0.6" stop-color="#4f8fe6"/>
        <stop offset="1" stop-color="#ffffff" stop-opacity="0.5"/>
      </linearGradient>
    </defs>
    <path d="M0 390 C 260 430, 520 480, 760 470 C 960 460, 1100 430, 1200 400 L1200 686 L0 686 Z" fill="url(#haze)"/>
    <path d="M0 580 C 300 580, 600 540, 860 490 C 1000 465, 1120 450, 1200 460 L1200 510 C 1050 495, 900 535, 700 585 C 500 630, 250 645, 0 655 Z" fill="url(#light)" opacity="0.6"/>
    <path d="M0 670 C 300 645, 600 610, 820 560 C 980 525, 1100 510, 1200 515 L1200 535 C 1080 535, 960 565, 800 605 C 600 650, 300 680, 0 686 Z" fill="url(#swoosh)"/>
    <path d="M0 686 C 400 665, 800 650, 1200 615 L1200 686 Z" fill="#ffffff" opacity="0.6"/>
  </svg>

  <p class="card__license">LICENSE NO: 73840</p>
  <p class="card__contact">DECLAN KETTERING | 0432961085</p>
  <p class="card__email">d_kettering@mailwave.com.au</p>

  <h1 class="brand">
    <span class="brand__name">Kettering Plumbing</span>
    <span class="brand__tagline">&amp; gas fitting</span>
  </h1>

  <p class="services">NEW HOMES | MAINTENANCE | RENOVATIONS</p>

  <div class="card__illustration" role="img" aria-label="Silhouette illustration of a plumber kneeling beside a pipe with a toolbox"></div>
</main>
</body>
</html>
```